Acupuncture business needs business card design

I need a business card for an acupuncture clinic called "Harbourlight Wellness"
It will need the following details:
My name: Marcus Pelling
Acupuncturist
Member TVBH
KWF Treatment Provider
Ph numbers: 581 2734 027 418 5620
Email: marcus@hbwel.example.nz
On the back it will need a table with 2 columns for appointments, one column for time and one for date.

Industry/Entity Type

Clinic

Contact Information for Business Card

Marcus Pelling
Acupuncturist
Member TVBH
KWF Treatment Provider
Email: marcus@hbwel.example.nz

Requirements
Must have
• Marcus Pelling
• Acupuncturist
• Member TVBH
• KWF Treatment Provider
• Ph numbers: 581 2734 027 418 5620
• Email: marcus@hbwel.example.nz
• On the back it will need a table with 2 columns for appointments, one column for time and one for date.

```html
<!DOCTYPE html>
<html lang="en">
<head>
<meta charset="utf-8">
<title>Harbourlight Wellness – Business Card</title>
<link href="https://fonts.googleapis.com/css2?family=Open+Sans:wght@400;600&family=Roboto+Condensed:wght@400;700&display=swap" rel="stylesheet">
<style>
  :root{
    --page:#e9ebec;
    --card-black:#0b0c0d;
    --teal:#1b7f93;
    --teal-back:#137a8e;
    --sky:#37b5e6;
    --ink-light:#e8eef0;
    --ink-muted:#9fb4ba;
    --slot:#d3e6ea;
    --rule:#2a3034;
  }
  *{box-sizing:border-box;margin:0;padding:0}
  html,body{width:1200px;height:948px;overflow:hidden}
  body{
    background:var(--page);
    display:flex;flex-direction:column;align-items:center;justify-content:center;gap:56px;
    font-family:"Open Sans",sans-serif;
  }
  .card{
    width:700px;height:400px;border-radius:6px;position:relative;overflow:hidden;
    box-shadow:0 6px 18px rgba(0,0,0,.18);
  }

  /* Front */
  .card--front{background:var(--card-black);display:flex}
  .brand-mark{
    width:300px;display:flex;flex-direction:column;align-items:center;justify-content:center;gap:18px;
  }
  .brand-mark__dot{width:120px;height:120px;border-radius:50%;background:var(--teal)}
  .brand-mark__name{
    font-family:"Roboto Condensed",sans-serif;font-weight:400;font-size:24px;color:var(--teal);
    text-align:center;line-height:1.15;
  }
  .divider{width:1px;background:var(--rule);margin:48px 0}
  .details{flex:1;padding:56px 40px 0 38px;color:var(--ink-light)}
  .company{
    font-family:"Roboto Condensed",sans-serif;font-weight:400;font-size:34px;color:var(--sky);line-height:1;
  }
  .tagline{font-size:9.5px;letter-spacing:2.6px;color:var(--teal);text-transform:uppercase;margin-top:6px}
  .person{margin-top:38px}
  .person__name{font-family:"Roboto Condensed",sans-serif;font-weight:700;font-size:20px;color:var(--sky)}
  .person__role{font-size:13px;color:var(--teal);line-height:1.5}
  .contact{margin-top:26px;font-size:15px;list-style:none}
  .contact li{display:flex;align-items:center;gap:12px;margin-bottom:9px}
  .contact svg{width:16px;height:16px;flex:none}

  /* Back */
  .card--back{background:var(--teal-back);padding:46px 60px;color:var(--ink-light)}
  .back-watermark{
    position:absolute;left:50%;top:50%;transform:translate(-50%,-50%);
    font-family:"Roboto Condensed",sans-serif;font-weight:700;font-size:64px;color:#fff;opacity:.09;white-space:nowrap;
  }
  .appointments{position:relative;width:100%;border-collapse:separate;border-spacing:18px 14px}
  .appointments th{
    text-align:left;font-weight:400;font-size:17px;letter-spacing:1px;padding-left:2px;
  }
  .appointments td{height:30px;background:var(--slot);opacity:.9}
  .website{
    position:absolute;left:0;right:0;bottom:36px;text-align:center;
    font-size:20px;letter-spacing:4px;
  }
</style>
</head>
<body>

  <section class="card card--front" aria-label="Business card front">
    <div class="brand-mark">
      <span class="brand-mark__dot"></span>
      <span class="brand-mark__name">Harbourlight<br>Wellness</span>
    </div>
    <div class="divider"></div>
    <div class="details">
      <h1 class="company">Harbourlight Wellness</h1>
      <p class="tagline">Acupuncture Physiotherapy</p>
      <div class="person">
        <h2 class="person__name">Marcus Pelling</h2>
        <p class="person__role">Acupuncturist Member TVBH</p>
        <p class="person__role">KWF Treatment Provider</p>
      </div>
      <ul class="contact">
        <li>
          <svg viewBox="0 0 16 16" aria-hidden="true"><circle cx="8" cy="8" r="7.5" fill="#e8eef0"/><path d="M5.2 4.2l1.4-.3.8 2-1 .7c.5 1.1 1.3 1.9 2.3 2.4l.7-1 2 .8-.3 1.4c-3.1.2-6.1-2.8-5.9-6z" fill="#0b0c0d"/></svg>
          581 2734 · 027 418 5620
        </li>
        <li>
          <svg viewBox="0 0 16 16" aria-hidden="true"><rect x="1" y="3.5" width="14" height="9" rx="1.5" fill="#e8eef0"/><path d="M1.8 4.5L8 9l6.2-4.5" stroke="#0b0c0d" stroke-width="1.3" fill="none"/></svg>
          marcus@hbwel.example.nz
        </li>
      </ul>
    </div>
  </section>

  <section class="card card--back" aria-label="Business card back">
    <span class="back-watermark" aria-hidden="true">Harbourlight Wellness</span>
    <table class="appointments">
      <thead><tr><th>Time</th><th>Date</th></tr></thead>
      <tbody>
        <tr><td></td><td></td></tr>
        <tr><td></td><td></td></tr>
        <tr><td></td><td></td></tr>
        <tr><td></td><td></td></tr>
      </tbody>
    </table>
    <p class="website">www.hbwel.example.nz</p>
  </section>

</body>
</html>
```